Business Card Design

Hi I need a business card designed, we already have the business name logo artwork and would like some concept ideas for the Bus Card layout.
On the back of the card i want to include the products and services that we offer.
We are a Plastics Sheeting manufacture based in Perth Australia.

                                       

We need a BC design for a company called Tarvo Plastics based in Perth Australia.

We supply from DIY to Trade & Industrial  Engineering Markets.

We specialise in:

·         Cut to size panels  (all shapes and sizes)

·         Plastics fabrication & Welding

·         Custom Designs

·         Plastic Repairs

·         PVC Pipe Slotting & PVC Pipe Threading

·         Supplier of all types of engineering plastics and profiles.

Including:           Acrylic / Clarvene

                               Polycarbonate / Dorvil

                               Prismatic Light Diffuser

                               Vantrib

                               HDPE / UHMWPE

                               PVC / PVC Foam

                               Nylon

                               HIPS

```html
<!DOCTYPE html>
<html lang="en">
<head>
<meta charset="utf-8">
<title>Tarvo Plastics – Business Card</title>
<link href="https://fonts.googleapis.com/css2?family=Open+Sans:ital,wght@0,400;0,600;0,700;1,700&display=swap" rel="stylesheet">
<style>
  :root {
    --navy: #1d2a5c;
    --bullet-blue: #2a8fd0;
    --accent-orange: #e8862a;
    --text-grey: #4a4a4a;
    --card-white: #ffffff;
    --backdrop: #e6e6ec;
    --divider: #c9c9cf;
    --faint-mark: #eceef3;
  }
  * { box-sizing: border-box; margin: 0; padding: 0; }
  html, body {
    width: 1200px; height: 987px; overflow: hidden;
    background: var(--backdrop);
    font-family: "Open Sans", Arial, sans-serif;
  }
  .sheet {
    width: 1200px; height: 987px;
    display: flex; flex-direction: column; align-items: center; justify-content: center;
    gap: 40px;
  }
  .card {
    position: relative;
    width: 720px; height: 440px;
    background: var(--card-white);
    border-radius: 28px;
    box-shadow: 0 6px 18px rgba(0,0,0,0.12);
    overflow: hidden;
  }

  /* ---------- Back ---------- */
  .card-back { padding: 30px 40px; text-align: center; }
  .back-mark {
    position: absolute; left: 50%; top: 52%;
    transform: translate(-50%, -50%);
    font-size: 110px; font-weight: 700; color: var(--faint-mark);
    white-space: nowrap; z-index: 0;
  }
  .back-content { position: relative; z-index: 1; }
  .market-line {
    color: var(--navy); font-weight: 700; font-style: italic;
    font-size: 19px; line-height: 1.3;
  }
  .section-title {
    color: var(--navy); font-weight: 700; font-size: 23px;
    margin-top: 16px; margin-bottom: 6px;
  }
  .service-list {
    list-style: none; color: var(--text-grey);
    font-size: 16.5px; line-height: 1.55;
  }
  .service-list li span { white-space: nowrap; }
  .service-list li span + span { margin-left: 12px; }
  .dot {
    display: inline-block; width: 7px; height: 7px; border-radius: 50%;
    background: var(--bullet-blue); margin-right: 6px; vertical-align: middle;
    position: relative; top: -2px;
  }

  /* ---------- Front ---------- */
  .brand-name {
    position: absolute; left: 48px; top: 150px;
    font-size: 46px; font-weight: 700; color: var(--navy);
    letter-spacing: -0.5px;
  }
  .divider {
    position: absolute; left: 372px; top: 60px;
    width: 1px; height: 320px;
    background: linear-gradient(to bottom, transparent, var(--divider) 15%, var(--divider) 85%, transparent);
  }
  .contact-block {
    position: absolute; left: 398px; top: 62px; right: 24px;
    color: var(--text-grey);
  }
  .person-name { color: var(--navy); font-size: 30px; font-weight: 700; line-height: 1.1; }
  .person-title { color: var(--accent-orange); font-size: 18px; margin-bottom: 14px; }
  .contact-row {
    display: flex; align-items: center; gap: 10px;
    font-size: 19px; line-height: 1.6;
  }
  .contact-row svg { width: 18px; height: 18px; flex: none; fill: var(--navy); }
  .address { font-size: 19px; line-height: 1.4; margin-top: 8px; }
  .legal-line {
    position: absolute; left: 48px; bottom: 32px;
    font-size: 14px; color: var(--text-grey);
  }
</style>
</head>
<body>
<main class="sheet">

  <section class="card card-back" aria-label="Card back">
    <div class="back-mark" aria-hidden="true">Tarvo Plastics</div>
    <div class="back-content">
      <p class="market-line">The Products And Services That We Offer<br>Are Supplied From Diy To Trade &amp; Industrial Engineering Markets</p>

      <h2 class="section-title">We specialise in:</h2>
      <ul class="service-list">
        <li><span><i class="dot"></i>Cut to size panels (all shapes and sizes)</span></li>
        <li><span><i class="dot"></i>Plastics fabrication &amp; Welding</span><span><i class="dot"></i>Custom Designs</span></li>
        <li><span><i class="dot"></i>Plastic Repairs</span><span><i class="dot"></i>PVC Pipe Slotting &amp; PVC Pipe Threading</span></li>
        <li><span><i class="dot"></i>Supplier of all types of engineering plastics and profiles</span></li>
      </ul>

      <h2 class="section-title">Including:</h2>
      <ul class="service-list">
        <li><span><i class="dot"></i>Acrylic / Clarvene</span><span><i class="dot"></i>Polycarbonate / Dorvil</span></li>
        <li><span><i class="dot"></i>Prismatic Light Diffuser</span><span><i class="dot"></i>Vantrib</span><span><i class="dot"></i>HDPE / UHMWPE</span></li>
        <li><span><i class="dot"></i>PVC / PVC Foam</span><span><i class="dot"></i>Nylon</span><span><i class="dot"></i>HIPS</span></li>
      </ul>
    </div>
  </section>

  <section class="card card-front" aria-label="Card front">
    <div class="brand-name">Tarvo Plastics</div>
    <div class="divider"></div>

    <div class="contact-block">
      <div class="person-name">Your Name</div>
      <div class="person-title">Title</div>

      <div class="contact-row">
        <svg viewBox="0 0 24 24" aria-label="Phone"><circle cx="12" cy="12" r="11" fill="none" stroke="#1d2a5c" stroke-width="2"/><path d="M8 6.5l2 0 1 3-1.3 1a7 7 0 0 0 3.8 3.8l1-1.3 3 1v2a1.5 1.5 0 0 1-1.6 1.5A10 10 0 0 1 6.5 8.1 1.5 1.5 0 0 1 8 6.5z"/></svg>
        <span>08 9000 4117</span>
      </div>
      <div class="contact-row">
        <svg viewBox="0 0 24 24" aria-label="Mobile"><rect x="6" y="1" width="12" height="22" rx="2"/><rect x="8" y="4" width="8" height="9" fill="#fff"/><circle cx="12" cy="18" r="1.6" fill="#fff"/></svg>
        <span>123-456-7890</span>
      </div>
      <div class="contact-row">
        <svg viewBox="0 0 24 24" aria-label="Fax"><rect x="6" y="2" width="12" height="8" fill="none" stroke="#1d2a5c" stroke-width="2"/><rect x="2" y="9" width="20" height="11" rx="2"/><rect x="7" y="14" width="10" height="8" fill="#fff" stroke="#1d2a5c" stroke-width="1.5"/></svg>
        <span>08 9000 4128</span>
      </div>
      <div class="contact-row">
        <svg viewBox="0 0 24 24" aria-label="Email"><rect x="1" y="5" width="22" height="15" rx="2"/><path d="M2 6l10 8 10-8" fill="none" stroke="#fff" stroke-width="2"/></svg>
        <span>sales@tarvoplastics.com.au</span>
      </div>

      <div class="address">
        Unit 4/18 Harlow Circuit<br>
        Brenmore WA 6155<br>
        PO Box 2240<br>
        Brenmore DC WA 6970
      </div>
    </div>

    <div class="legal-line">Kestrel Trading Pty Ltd T/A Tarvo Plastics ABN: TBA</div>
  </section>

</main>
</body>
</html>
```